Clear Harbor Business card

We are a company that owns 2 compliance software programs for TV, Radio and Cable industries as well as an online job board. We need a professional business card that incorproates all three logos.

```html
<!DOCTYPE html>
<html lang="en">
<head>
<meta charset="utf-8">
<title>Clear Harbor Business Card</title>
<link href="https://fonts.googleapis.com/css2?family=Roboto:wght@400;500;700&display=swap" rel="stylesheet">
<style>
  :root {
    --navy: #15135e;
    --red: #e2381f;
    --paper: #f4f4f2;
    --white: #ffffff;
    --backdrop: #1c1c1e;
  }
  * { margin: 0; padding: 0; box-sizing: border-box; }
  html, body {
    width: 1200px; height: 874px; overflow: hidden;
    background: var(--backdrop);
    font-family: "Roboto", Arial, sans-serif;
  }
  .card {
    position: absolute; left: 290px;
    width: 620px; height: 354px;
    overflow: hidden;
    box-shadow: 0 10px 30px rgba(0,0,0,.45);
  }
  .card-back { top: 54px; background: var(--navy); }
  .card-front { top: 466px; background: var(--navy); }

  .brand-row {
    position: absolute; display: flex; align-items: center;
  }
  .brand-name {
    font-weight: 700; font-size: 17px; line-height: 1.05;
    white-space: nowrap;
  }
  .brand-divider { width: 1.5px; height: 46px; margin: 0 14px; }

  .card-back .brand-row { left: 0; right: 0; top: 138px; justify-content: center; }
  .card-back .brand-name { color: var(--white); }
  .card-back .brand-divider { background: var(--white); }
  .brand-dot {
    display: inline-block; width: 14px; height: 14px; border-radius: 50%;
    margin-right: 7px; vertical-align: -1px;
  }
  .card-back .brand-dot { border: 2.5px solid var(--white); }
  .back-url {
    position: absolute; left: 0; right: 0; top: 262px; text-align: center;
    color: var(--white); font-size: 15px; letter-spacing: 7px;
  }

  .front-art { position: absolute; inset: 0; }
  .holder {
    position: absolute; left: 38px; top: 34px; color: var(--white);
  }
  .holder-name { font-size: 24px; font-weight: 700; letter-spacing: .5px; }
  .holder-title { font-size: 15px; margin-top: 2px; }
  .contact {
    position: absolute; left: 38px; top: 150px; color: var(--white);
    font-size: 15px; line-height: 21px;
  }
  .address { margin-bottom: 4px; }
  .contact-line { display: flex; align-items: center; }
  .contact-line svg { width: 14px; height: 14px; margin-right: 10px; fill: var(--white); flex: none; }

  .card-front .brand-row { left: 290px; top: 160px; }
  .card-front .brand-name { color: var(--navy); font-size: 14px; }
  .card-front .brand-divider { background: var(--navy); height: 40px; margin: 0 10px; }
  .card-front .brand-dot { border: 2.5px solid var(--navy); width: 12px; height: 12px; }
</style>
</head>
<body>

<section class="card card-back" aria-label="Card back">
  <div class="brand-row">
    <span class="brand-name">Clear Harbor<br>Air</span>
    <span class="brand-divider"></span>
    <span class="brand-name">Clear Harbor<br>Cable</span>
    <span class="brand-divider"></span>
    <span class="brand-name"><span class="brand-dot"></span>CrewBoard</span>
  </div>
  <p class="back-url">www.clearharbor.example</p>
</section>

<section class="card card-front" aria-label="Card front">
  <svg class="front-art" viewBox="0 0 620 354" preserveAspectRatio="none" aria-hidden="true">
    <path d="M362,0 C300,70 262,200 262,354" fill="none" stroke="var(--red)" stroke-width="9"/>
    <path d="M372,0 C312,70 274,200 274,354 L620,354 L620,0 Z" fill="var(--paper)"/>
  </svg>

  <div class="holder">
    <p class="holder-name">DANA WHITFIELD</p>
    <p class="holder-title">CEO/FOUNDER</p>
  </div>

  <div class="contact">
    <p class="address">214 Quayside Road<br>Portland, Maine 04101</p>
    <p class="contact-line">
      <svg viewBox="0 0 24 24"><path d="M6.6 10.8c1.4 2.8 3.8 5.1 6.6 6.6l2.2-2.2c.3-.3.7-.4 1-.2 1.1.4 2.3.6 3.6.6.6 0 1 .4 1 1V20c0 .6-.4 1-1 1C10.6 21 3 13.4 3 4c0-.6.4-1 1-1h3.5c.6 0 1 .4 1 1 0 1.3.2 2.5.6 3.6.1.3 0 .7-.2 1z"/></svg>555 201 4417</p>
    <p class="contact-line">
      <svg viewBox="0 0 24 24"><path d="M7 1h10a2 2 0 0 1 2 2v18a2 2 0 0 1-2 2H7a2 2 0 0 1-2-2V3a2 2 0 0 1 2-2zm0 3v14h10V4z"/></svg>555 390 2281</p>
    <p class="contact-line">
      <svg viewBox="0 0 24 24"><path d="M6 2h12v6H6zM3 9h18a1 1 0 0 1 1 1v8h-4v4H6v-4H2v-8a1 1 0 0 1 1-1zm5 8v3h8v-3z"/></svg>555 764 0192</p>
    <p class="contact-line">
      <svg viewBox="0 0 24 24"><path d="M2 5h20v14H2zm2 2v.5l8 5 8-5V7l-8 5z"/></svg>dana@clearharbor.example</p>
    <p class="contact-line">
      <svg viewBox="0 0 24 24"><path d="M12 2a10 10 0 1 0 0 20 10 10 0 0 0 0-20zm-1 17.9A8 8 0 0 1 4.1 10L9 15v1a2 2 0 0 0 2 2zm6.9-2.5A2 2 0 0 0 16 16h-1v-3a1 1 0 0 0-1-1H8v-2h2a1 1 0 0 0 1-1V7h2a2 2 0 0 0 2-2v-.4a8 8 0 0 1 2.9 12.8z"/></svg>www.clearharbor.example</p>
  </div>

  <div class="brand-row">
    <span class="brand-name">Clear Harbor<br>Air</span>
    <span class="brand-divider"></span>
    <span class="brand-name">Clear Harbor<br>Cable</span>
    <span class="brand-divider"></span>
    <span class="brand-name"><span class="brand-dot"></span>CrewBoard</span>
  </div>
</section>

</body>
</html>
```